The most modern business card ever !!!

Our company call “Vendalo”. Vendalo is a technology company specialized in cruises solutions. Out main product is a platform to reserve cruises. This is a revolutionary platform that make easier to travel agencies and final users to reserve cruises across dozen companies like tibba, wernu, hpv, dgb, etc..We are a “start up”, with a young team of developers and we want to transmit it.. For it, we want something different, a modern business card that represent cruises and technology.. When someone receive this card, this person should say: wowww this is different… this is modern… this is a cruise related company..
- diferent, modern
- traditions business card

```html
<!DOCTYPE html>
<html lang="en">
<head>
<meta charset="utf-8">
<title>Vendalo Business Card</title>
<link href="https://fonts.googleapis.com/css2?family=Exo+2:wght@400;500;600;700&display=swap" rel="stylesheet">
<style>
  :root {
    --backdrop: #7b7b7b;
    --card-light: #eeeeee;
    --card-dark: #0d0d0d;
    --ink: #1a1a1a;
    --ink-soft: #2b2b2b;
    --accent: #29a3dc;
    --rule: #9a9a9a;
    --white: #ffffff;
  }
  html, body {
    margin: 0;
    width: 1200px;
    height: 1200px;
    overflow: hidden;
    background: var(--backdrop);
  }
  .canvas {
    position: relative;
    width: 1200px;
    height: 1200px;
    font-family: "Exo 2", sans-serif;
  }
  .card {
    position: absolute;
    top: 310px;
    width: 366px;
    height: 595px;
    box-sizing: border-box;
    text-align: center;
  }
  .card--front {
    left: 234px;
    background: var(--card-light);
    color: var(--ink-soft);
  }
  .card--back {
    left: 628px;
    width: 370px;
    background: linear-gradient(180deg, #111111 0%, var(--card-dark) 60%, #090909 100%);
    color: var(--white);
  }
  .wordmark {
    position: absolute;
    left: 0;
    right: 0;
    font-weight: 500;
    font-size: 64px;
    letter-spacing: 1px;
    line-height: 1;
  }
  .card--front .wordmark { top: 142px; color: var(--ink); }
  .card--back .wordmark { top: 268px; color: var(--white); }
  .holder {
    position: absolute;
    top: 342px;
    left: 0;
    right: 0;
  }
  .holder__name {
    font-weight: 700;
    font-size: 24px;
    color: var(--accent);
    letter-spacing: 0.5px;
    line-height: 28px;
    text-transform: uppercase;
  }
  .holder__role {
    font-size: 18px;
    line-height: 22px;
  }
  .rule {
    width: 208px;
    height: 1px;
    background: var(--rule);
    margin: 8px auto 10px;
  }
  .contact {
    font-size: 18px;
    line-height: 24.5px;
  }
  .contact__label {
    font-weight: 700;
    color: var(--accent);
  }
  .contact__web {
    font-weight: 700;
    color: var(--accent);
  }
  .address {
    font-size: 18px;
    line-height: 24.5px;
  }
  .card--back .site {
    position: absolute;
    left: 0;
    right: 0;
    top: 526px;
    font-size: 20px;
    letter-spacing: 0.5px;
  }
</style>
</head>
<body>
<main class="canvas">
  <section class="card card--front">
    <div class="wordmark">Vendalo</div>
    <div class="holder">
      <div class="holder__name">Marcus Hale</div>
      <div class="holder__role">Managing Director</div>
      <div class="rule"></div>
      <div class="contact">
        <div><span class="contact__label">P:</span> 044-580 214 376</div>
        <div><span class="contact__label">M:</span> 044-580 214 376</div>
        <div><span class="contact__label">E:</span> hello@vendalo.io</div>
        <div class="contact__web">www.vendalo.io</div>
      </div>
      <div class="rule"></div>
      <div class="address">
        <div>48, Harbour Lane West</div>
        <div>Portland Bay, 560318.</div>
      </div>
    </div>
  </section>

  <section class="card card--back">
    <div class="wordmark">Vendalo</div>
    <div class="site">www.vendalo.io</div>
  </section>
</main>
</body>
</html>
```